Web Design Project

Psychotherapy and Counselling Practice needs a landing page web design.

My business "Larkfield Advisory" specialises in the treatment of Anxiety and Depression with a holistic approach, endeavouring to unlock the key that holds us to ransom in a life that is imbalanced, frustrating, and ultimately of our own making due to our own perceptions and behaviours.

There is much that impacts us which we cannot change, but we are always in control of how we think, and how we frame our experiences.....learning to challenge those thoughts and behaviours that are destructive and disempowering opens up a world of joyful possibility. Life is about making choices, learn to make wiser and healthier choices.......

Larkfield Advisory has a client base of individual clients but will seek to expand to offer services to the Corporate world by offering an adjunct to employers for established "Wellness Programs".

Larkfield Advisory is a highly professional, ethically bound business, with the needs of the client at the forefront of all we do.

Larkfield Advisory wishes to avoid the usual "jargon driven" psychobabble offered on many counselling web pages. It aims to be stylishly presented, clean in look and with as few "words" as possible and a largely white background (faster loading and more powerful impact of what is stated), those words contained in the webpage should be meaningful, persuasive and have an impact simply at glance. Larkfield does not want , or expect, those prospective clients in need of support , to be reading through volumes of industry driven cliches.

At this point Larkfield is just looking for a high quality landing page. However in time this will likely expand to include other sections such as case studies, video content etc.

Target Market(s)

Those in need of emotional support, suffering mental health issues, and those simply wanting to become self aware supported by a mindful therapist.

Industry/Entity Type

Industry

Requirements
Must have
• The design must incorporate the Larkfield logo and colour schemes found on the attached files.

```html
<!DOCTYPE html>
<html lang="en">
<head>
<meta charset="utf-8">
<title>Larkfield Advisory</title>
<link rel="stylesheet" href="https://fonts.googleapis.com/css2?family=Mulish:wght@300;400;700;800&display=swap">
<style>
  :root {
    --green: #86a70b;
    --green-bright: #a7c519;
    --slate: #595959;
    --ink: #4a4a4a;
    --muted: #6b6b6b;
    --field: #ffffff;
    --red-top: #d62a24;
    --red-bottom: #a8120f;
    --page: #efefef;
  }
  * { box-sizing: border-box; margin: 0; padding: 0; }
  html, body { width: 1200px; height: 942px; overflow: hidden; }
  body {
    font-family: "Mulish", Arial, sans-serif;
    color: var(--ink);
    background: radial-gradient(ellipse at 50% 30%, #ffffff 0%, #f6f6f6 45%, var(--page) 100%);
    position: relative;
  }
  .header-band {
    position: absolute; left: 0; top: 150px; width: 1000px; height: 140px;
    background: linear-gradient(180deg, rgba(134,167,11,0) 0%, rgba(134,167,11,.07) 45%, rgba(110,110,110,.09) 100%);
  }
  .brand {
    position: absolute; left: 232px; top: 98px;
    font-size: 40px; font-weight: 300; letter-spacing: 1px;
    color: var(--green);
  }
  .contact { position: absolute; right: 203px; top: 76px; text-align: right; }
  .contact-lead { font-size: 12.5px; color: var(--muted); }
  .contact-phone { font-size: 30px; color: var(--slate); line-height: 1.05; display: flex; align-items: center; justify-content: flex-end; gap: 4px; }
  .contact-email { font-size: 14.5px; color: var(--green); }

  .hero { position: absolute; left: 199px; top: 298px; width: 801px; height: 333px; display: flex; box-shadow: 0 14px 14px -10px rgba(0,0,0,.18); }
  .enquiry { width: 400px; background: var(--green); padding: 14px 31px 0 17px; }
  .enquiry h2 { color: #fff; font-size: 23px; font-weight: 800; letter-spacing: -0.6px; margin-bottom: 10px; white-space: nowrap; }
  .field { background: var(--field); height: 35px; display: flex; align-items: center; margin-bottom: 7px; border: 1px solid #9cba25; }
  .field.message { height: 75px; align-items: flex-start; padding-top: 8px; margin-top: 2px; }
  .field-icon { width: 37px; display: flex; justify-content: center; border-right: 1px solid #cfcfcf; height: 20px; align-items: center; }
  .field-label { padding-left: 10px; font-size: 14px; color: #6d6d6d; font-weight: 300; }
  .submit {
    display: block; margin: 10px 0 0 auto; width: 222px; height: 42px;
    background: linear-gradient(var(--red-top), var(--red-bottom));
    border: 1px solid #7c0c0a; color: #fff; font-family: inherit;
    font-size: 27px; font-weight: 800; letter-spacing: -1px;
    text-shadow: 0 2px 2px rgba(0,0,0,.45);
  }
  .promise { flex: 1; background: var(--slate); color: #fff; padding: 126px 0 0 41px; font-weight: 300; }
  .promise p { line-height: 1.12; white-space: nowrap; }
  .promise .lead { font-size: 18px; letter-spacing: -0.3px; }
  .promise .small { font-size: 16px; }
  .promise .accent { color: var(--green-bright); font-size: 22px; font-weight: 400; letter-spacing: -0.3px; }
  .promise .big { font-size: 26px; letter-spacing: -0.4px; }

  .feature { position: absolute; top: 684px; }
  .feature-title { display: flex; align-items: center; gap: 14px; font-size: 19px; color: var(--green); font-weight: 300; height: 28px; white-space: nowrap; }
  .feature p { margin-top: 19px; width: 205px; font-size: 10.4px; line-height: 13.5px; color: #555; font-weight: 300; }
  .read-more { display: block; margin-top: 15px; font-size: 12px; color: #444; font-weight: 300; }
  .wellness { left: 211px; }
  .cases { left: 490px; }
  .video { left: 752px; }
  .divider { position: absolute; top: 688px; height: 143px; border-left: 1px dotted #b5b5b5; }
  .divider.one { left: 452px; }
  .divider.two { left: 722px; }
  .video-thumb {
    margin-top: 14px; width: 238px; height: 108px; border: 2px solid #d8d8d8;
    background: linear-gradient(#f3f3f3, #e6e6e6);
    display: flex; align-items: center; justify-content: center;
  }
  .play { width: 38px; height: 38px; border-radius: 50%; background: #fff; border: 3px solid #9b9b9b; display: flex; align-items: center; justify-content: center; }

  .footer-rule { position: absolute; left: 202px; top: 877px; width: 796px; border-top: 1px dotted #b0b0b0; }
  .legal { position: absolute; left: 204px; top: 900px; font-size: 11.5px; color: #555; font-weight: 300; }
  .legal .firm { color: var(--green); font-size: 15px; }
  .social { position: absolute; left: 901px; top: 902px; display: flex; gap: 6px; }
  .social span { width: 12px; height: 12px; background: #6a6a6a; border-radius: 2px; }
</style>
</head>
<body>
  <div class="header-band" role="img" aria-label="Decorative green and grey header sweep"></div>

  <div class="brand">LARKFIELD</div>

  <div class="contact">
    <div class="contact-lead">For Appointmet Call Us Today</div>
    <div class="contact-phone">
      <svg width="24" height="24" viewBox="0 0 24 24" aria-hidden="true"><path d="M6.6 10.8a15 15 0 0 0 6.6 6.6l2.2-2.2c.3-.3.7-.4 1-.2 1.1.4 2.3.6 3.6.6.6 0 1 .4 1 1V20c0 .6-.4 1-1 1A17 17 0 0 1 3 4c0-.6.4-1 1-1h3.5c.6 0 1 .4 1 1 0 1.3.2 2.5.6 3.6.1.3 0 .7-.2 1z" fill="var(--green)"/></svg>
      0400 118 276
    </div>
    <div class="contact-email">hello@larkfieldadvisory.com</div>
  </div>

  <section class="hero">
    <form class="enquiry">
      <h2>GET MORE INFORMATION</h2>
      <div class="field"><span class="field-icon"><svg width="18" height="20" viewBox="0 0 18 20"><circle cx="9" cy="5" r="4" fill="#666"/><path d="M1 20c0-6 3-9 8-9s8 3 8 9z" fill="#666"/></svg></span><span class="field-label">Enter Your Name</span></div>
      <div class="field"><span class="field-icon"><svg width="22" height="16" viewBox="0 0 22 16"><rect x="1" y="1" width="20" height="14" fill="none" stroke="#666" stroke-width="2"/><path d="M1 1l10 8 10-8" fill="none" stroke="#666" stroke-width="2"/></svg></span><span class="field-label">Enter Your Email</span></div>
      <div class="field"><span class="field-icon"><svg width="16" height="16" viewBox="0 0 24 24"><path d="M6.6 10.8a15 15 0 0 0 6.6 6.6l2.2-2.2c.3-.3.7-.4 1-.2 1.1.4 2.3.6 3.6.6.6 0 1 .4 1 1V20c0 .6-.4 1-1 1A17 17 0 0 1 3 4c0-.6.4-1 1-1h3.5c.6 0 1 .4 1 1 0 1.3.2 2.5.6 3.6.1.3 0 .7-.2 1z" fill="#666"/></svg></span><span class="field-label">Enter Your Phone</span></div>
      <div class="field message"><span class="field-icon"><svg width="18" height="18" viewBox="0 0 18 18"><rect x="1" y="2" width="12" height="15" fill="none" stroke="#666" stroke-width="1.5"/><path d="M8 12l8-8" stroke="#666" stroke-width="2"/></svg></span><span class="field-label">Your Message Here...</span></div>
      <button class="submit" type="submit">SUBMIT NOW!</button>
    </form>
    <div class="promise">
      <p class="lead">SPECIALISES IN THE TREATMENT</p>
      <p><span class="small">OF </span><span class="accent">ANXIETY AND DEPRESSION</span></p>
      <p><span class="small">WITH </span><span class="big">HOLISTIC APPROACH</span></p>
    </div>
  </section>

  <article class="feature wellness">
    <div class="feature-title"><svg width="28" height="24" viewBox="0 0 28 24"><path d="M14 23L2 11A6.5 6.5 0 0 1 14 4a6.5 6.5 0 0 1 12 7z" fill="#6a6a6a"/></svg>Wellness Programs</div>
    <p>Lorem ipsum dolor sit amet, consectetuer adipiscing elit, sed diam nonummy nibh euismod tincidunt ut laoreet dolore magna aliquam erat volutpat. Ut wisi enim ad minim veniam, quis nostrud exerci tation ullamcorper suscipit lobortis...</p>
    <span class="read-more">Read More...</span>
  </article>
  <div class="divider one"></div>
  <article class="feature cases">
    <div class="feature-title"><svg width="30" height="22" viewBox="0 0 30 22"><path d="M1 2h11c2 0 3 1 3 3v16c0-1-1-2-3-2H1z M29 2H18c-2 0-3 1-3 3v16c0-1 1-2 3-2h11z" fill="none" stroke="#6a6a6a" stroke-width="2"/></svg>Case Studies</div>
    <p>Lorem ipsum dolor sit amet, consectetuer adipiscing elit, sed diam nonummy nibh euismod tincidunt ut laoreet dolore magna aliquam erat volutpat. Ut wisi enim ad minim veniam, quis nostrud exerci tation ullamcorper suscipit lobortis...</p>
    <span class="read-more">Read More...</span>
  </article>
  <div class="divider two"></div>
  <article class="feature video">
    <div class="feature-title"><svg width="24" height="22" viewBox="0 0 24 22"><rect x="1" y="7" width="22" height="14" fill="#6a6a6a"/><path d="M1 2h22v4H1z" fill="#6a6a6a"/></svg>Watch Video</div>
    <div class="video-thumb" role="img" aria-label="Video preview with the Larkfield name">
      <span class="play"><svg width="14" height="16" viewBox="0 0 14 16"><path d="M2 1l11 7-11 7z" fill="#222"/></svg></span>
    </div>
  </article>

  <div class="footer-rule"></div>
  <div class="legal">© 2013 <span class="firm">Larkfieldadvisory</span>. All rights reserved</div>
  <div class="social" aria-label="Social links"><span></span><span></span><span></span><span></span><span></span></div>
</body>
</html>
```